Website for Torvel Capital - investment banking firm

We have a corporate identity (thanks to Ravinka/31842) and want to extend that into a website design.  See the attached zipped files.
We have software folks in-house to do the coding.
See the attached Project Brief & Notes for more details.  Don't worry about the actual text - lorem ipsum will be fine.
The server will be Apache.
Thank you!
Desmond

Industry/Entity Type
Investment

```html
<!DOCTYPE html>
<html lang="en">
<head>
<meta charset="utf-8">
<title>Torvel Capital</title>
<link rel="stylesheet" href="https://fonts.googleapis.com/css2?family=Open+Sans:wght@400;600&family=Oswald:wght@300;400&family=Marcellus+SC&family=Roboto+Slab:wght@400;600&display=swap">
<style>
:root{
  --brand:#214c93;
  --brand-dark:#1c4185;
  --heading:#1f4e96;
  --text:#666;
  --text-dark:#333;
  --rule:#e3e3e3;
  --accent-red:#b3261e;
  --white:#fff;
}
*{box-sizing:border-box;margin:0;padding:0}
html,body{width:929px;height:1200px;overflow:hidden;background:var(--white)}
body{font-family:"Open Sans",sans-serif;color:var(--text)}
.page{position:relative;width:929px;height:1200px;overflow:hidden}
.abs{position:absolute}

/* header */
.brand{left:78px;top:28px;display:flex;align-items:center;gap:12px}
.brand-mark{width:36px;height:36px;background:var(--brand)}
.brand-name{font-family:"Marcellus SC",serif;font-size:25px;color:var(--brand);letter-spacing:.5px}
.search{left:618px;top:38px;width:233px;height:29px;border:1px solid #d6d6d6;display:flex}
.search span{flex:1;font-size:9px;color:#888;padding:8px 0 0 8px}
.search-btn{width:29px;height:29px;margin:-1px -1px 0 0;background:var(--brand);display:flex;align-items:center;justify-content:center}

.nav{left:0;top:100px;width:929px;height:32px;border-bottom:4px solid var(--brand)}
.nav a{position:absolute;top:0;height:28px;line-height:28px;font-size:11.5px;color:#666;text-decoration:none}
.nav .active{left:78px;width:54px;background:var(--brand);color:var(--white);font-weight:600;text-align:center}

/* hero */
.hero{left:0;top:132px;width:929px;height:348px;background:linear-gradient(100deg,#5d6f8a 0%,#c9d3df 30%,#eef1f5 55%,#b9c1cb 80%,#6a7587 100%)}
.hero-card{left:78px;top:187px;width:407px;height:240px;background:rgba(255,255,255,.78);padding:20px 20px 20px 24px}
.hero-card h1{font-family:"Oswald",sans-serif;font-weight:300;font-size:21px;line-height:33px;letter-spacing:-.3px;color:var(--brand)}
.hero-card p{font-size:10px;line-height:16px;color:#444;margin-top:17px}
.hero-btn{position:absolute;left:25px;top:183px;width:129px;height:35px;background:var(--brand);color:var(--white);font-size:10.5px;line-height:35px;text-align:center}
.hero-arrow{top:304px;width:20px;height:20px;border-radius:50%;background:rgba(255,255,255,.45);display:flex;align-items:center;justify-content:center}

/* services band */
.services{left:0;top:480px;width:929px;height:140px;background:var(--brand)}
.service{top:30px;width:180px;color:var(--white)}
.service h3{font-family:"Oswald",sans-serif;font-weight:300;font-size:15.5px;display:flex;align-items:center;gap:6px;white-space:nowrap}
.service .dot{width:18px;height:18px;border:1.5px solid var(--white);border-radius:50%;flex:none;position:relative}
.service .dot.on::after{content:"";position:absolute;left:4px;top:4px;width:7px;height:7px;border-radius:50%;background:var(--white)}
.service p{font-size:8px;line-height:12.6px;margin:6px 0 0 24px;text-align:justify}
.service .more{font-size:8px;margin:6px 0 0 24px}
.service .more.dark{color:#111}

/* who we are */
.section-title{font-size:14.5px;font-weight:600;color:var(--heading)}
.who-img{left:80px;top:684px;width:114px;height:114px;background:linear-gradient(135deg,#d9d3cc,#bba99d 55%,#eae6e2)}
.sub-title{font-size:12.5px;font-weight:600;color:#555}
.body-copy{font-size:9px;line-height:12.6px;color:#777}
.read-more{left:492px;top:847px;font-size:9.5px;color:var(--accent-red)}
.map{left:573px;top:686px;width:281px;height:172px;background:linear-gradient(90deg,#3e8fd0,#6fb2e3 50%,#3b86c9);box-shadow:2px 3px 4px rgba(0,0,0,.2)}

/* testimonials */
.testi-title{left:0;top:918px;width:929px;text-align:center;font-size:14.5px;font-weight:600;color:var(--heading)}
.testimonial{top:958px;width:270px;height:110px}
.avatar{position:absolute;left:0;top:0;width:56px;height:56px;border-radius:50%;border:3px solid #eee;background:linear-gradient(#9a8a7d,#5b4a3f)}
.quote-mark{position:absolute;left:80px;top:-10px;font-family:"Roboto Slab",serif;font-weight:600;font-size:52px;color:#ddd;line-height:1}
.quote{position:absolute;left:80px;top:28px;width:170px;font-family:"Roboto Slab",serif;font-size:8.6px;line-height:14px;color:#333;text-align:justify;text-indent:33px;hyphens:none}
.who-name{position:absolute;left:80px;top:76px;font-family:"Roboto Slab",serif;font-size:9.5px;font-weight:600;color:#333}
.role{position:absolute;left:80px;top:94px;font-size:7px;color:#999}
.role span{color:#3a70c4}

/* footer */
.footer{left:0;top:1122px;width:929px;height:78px;background:var(--brand-dark)}
.footer-line{left:0;top:40px;width:929px;height:1px;background:rgba(255,255,255,.15)}
.footer-text{left:0;width:929px;text-align:center;font-size:9.8px;color:var(--white)}
.to-top{left:830px;top:27px;width:27px;height:27px;border:1px solid rgba(255,255,255,.8);display:flex;align-items:center;justify-content:center}
</style>
</head>
<body>
<div class="page">

  <header>
    <div class="brand abs"><div class="brand-mark"></div><span class="brand-name">Torvel Capital</span></div>
    <div class="search abs"><span>Search for</span>
      <div class="search-btn"><svg width="14" height="14" viewBox="0 0 14 14"><circle cx="6" cy="6" r="4.5" fill="none" stroke="#fff" stroke-width="1.5"/><line x1="9.3" y1="9.3" x2="13" y2="13" stroke="#fff" stroke-width="1.5"/></svg></div>
    </div>
    <nav class="nav abs">
      <a class="active">Home</a>
      <a style="left:173px">About</a>
      <a style="left:250px">Services</a>
      <a style="left:340px">Current Engagements</a>
      <a style="left:505px">Completed Transactions</a>
    </nav>
  </header>

  <section class="hero abs" role="img" aria-label="Photo of two colleagues talking in an office"></section>
  <div class="hero-arrow abs" style="left:32px"><svg width="8" height="10"><path d="M6 1 2 5l4 4" fill="none" stroke="#fff" stroke-width="1.5"/></svg></div>
  <div class="hero-arrow abs" style="left:877px"><svg width="8" height="10"><path d="M2 1l4 4-4 4" fill="none" stroke="#fff" stroke-width="1.5"/></svg></div>
  <div class="hero-card abs">
    <h1>Maecenas Egestas Neque In Sapien Convallis Non Elementum Nibh Pharetra.</h1>
    <p>Maecenas mauris velit, consequat sit amet pharetra ut, ultricies vitae mi. Duis tempus mattis sem id placerat. Sed et risus non erat feugiat tempus in sed arcu. Mauris eu sem purus.</p>
    <div class="hero-btn">Show More Details</div>
  </div>

  <section class="services abs">
    <div class="service abs" style="left:78px"><h3><span class="dot"></span>Strategic Advisory Services</h3><p>We assist corporate clients and private equity groups to identify opportunities for growth by acquisition</p><div class="more">Read More →</div></div>
    <div class="service abs" style="left:277px"><h3><span class="dot on"></span>Current Engagements</h3><p>We assist corporate clients and private equity groups to identify opportunities for growth by acquisition</p><div class="more dark">Read More →</div></div>
    <div class="service abs" style="left:475px"><h3><span class="dot"></span>Completed Transactions</h3><p>We assist corporate clients and private equity groups to identify opportunities for growth by acquisition</p><div class="more">Read More →</div></div>
    <div class="service abs" style="left:674px"><h3><span class="dot"></span>Regulatory Compliance</h3><p>We assist corporate clients and private equity groups to identify opportunities for growth by acquisition</p><div class="more">Read More →</div></div>
  </section>

  <section class="who">
    <h2 class="section-title abs" style="left:78px;top:648px">Who We Are</h2>
    <div class="who-img abs" role="img" aria-label="Man sketching a process flow diagram"></div>
    <h3 class="sub-title abs" style="left:208px;top:680px">Our Clients</h3>
    <p class="body-copy abs" style="left:211px;top:705px;width:330px">Torvel Capital has a diverse array of clients ranging from multi-billion dollar strategic acquirers to large private equity funds. We will not engage a client as a buyer if we believe there is any chance of them wasting our time or a prospective seller's time</p>
    <h3 class="sub-title abs" style="left:209px;top:762px">Our Process</h3>
    <p class="body-copy abs" style="left:212px;top:786px">o&nbsp;&nbsp;&nbsp;&nbsp;&nbsp;&nbsp;&nbsp;&nbsp;Technology</p>
    <p class="body-copy abs" style="left:77px;top:811px;width:465px">o&nbsp;&nbsp;&nbsp;&nbsp;&nbsp;&nbsp;&nbsp;Once we have your acquisition parameters, we feed these into our software to create aninitial target list. The criteria used to create this list can include geography, revenue targets, earning targets, margins, shareholder structure, etc.</p>
    <div class="read-more abs">Read More</div>
  </section>

  <section class="global">
    <h2 class="section-title abs" style="left:558px;top:648px">Global Investment Banking Services</h2>
    <div class="map abs" role="img" aria-label="Folded world map with location pins"></div>
  </section>

  <section class="testimonials">
    <h2 class="testi-title abs">Testimonials</h2>
    <div class="testimonial abs" style="left:78px"><div class="avatar" role="img" aria-label="Client portrait"></div><div class="quote-mark">“</div><p class="quote">Pellentesque et pulvinar enim. Quisque at tempor ligula. Donec ut purus sed tortor malesuada.</p><div class="who-name">Marlo Fenwick</div><div class="role">Art Director / <span>lorem ipsum</span></div></div>
    <div class="testimonial abs" style="left:346px"><div class="avatar" role="img" aria-label="Client portrait"></div><div class="quote-mark">“</div><p class="quote">Pellentesque et pulvinar enim. Quisque at tempor ligula. Donec ut purus sed tortor malesuada.</p><div class="who-name">Marlo Fenwick</div><div class="role">Art Director / <span>lorem ipsum</span></div></div>
    <div class="testimonial abs" style="left:610px"><div class="avatar" role="img" aria-label="Client portrait"></div><div class="quote-mark">“</div><p class="quote">Pellentesque et pulvinar enim. Quisque at tempor ligula. Donec ut purus sed tortor malesuada.</p><div class="who-name">Marlo Fenwick</div><div class="role">Art Director / <span>lorem ipsum</span></div></div>
  </section>

  <footer class="footer abs">
    <p class="footer-text abs" style="top:13px">Desmond Hartwell&nbsp; - &nbsp;555.302.4187(m)&nbsp; - &nbsp;dhartwell@torvelcapital.com</p>
    <div class="footer-line abs"></div>
    <p class="footer-text abs" style="top:53px">Yoursite.com © 2014 All Rights Reserved.</p>
    <div class="to-top abs"><svg width="10" height="7"><path d="M1 6l4-4 4 4" fill="none" stroke="#fff" stroke-width="1.5"/></svg></div>
  </footer>

</div>
</body>
</html>
```